New web design for a service provider in the medical field

We are looking for a new design for our website. We are a company that repairs and sells medical endoscopes. Our customers include doctors and hospitals. Our current website can be found at https://lumavex.de/en/lumavex-english.
We need a new web design (without programming) for the following 3 pages:
-Startpage https://lumavex.de/en/lumavex-english/
-Used endoscopes https://lumavex.de/en/used-endoscopes/
-Purchase https://lumavex.de/en/purchase/
The design should be modern and stylish.
The blue color of the logo should be reflected on the page, but not too intrusive.
I have uploaded the images from the header. If more images are needed, let me know and I will upload them.

Target Market(s)
Doctors and hospitals

```html
<!DOCTYPE html>
<html lang="en">
<head>
<meta charset="utf-8">
<title>Lumavex – Endoscope Repair and Sale</title>
<link href="https://fonts.googleapis.com/css2?family=Nunito:wght@300;400;700;800;900&family=Roboto:wght@300;400;500;700&display=swap" rel="stylesheet">
<style>
:root{
  --blue:#1565c0;
  --navy:#0d47a1;
  --sky:#2f8fe0;
  --light:#eaf4fb;
  --mist:#eef0f3;
  --ink:#1b1f2a;
  --text:#4a505c;
  --muted:#7a808c;
  --white:#ffffff;
  --footer:#0b0b0d;
}
*{box-sizing:border-box;margin:0;padding:0}
html,body{width:1200px;height:5115px;overflow:hidden}
body{font-family:"Roboto",sans-serif;color:var(--text);background:var(--white);position:relative}
.abs{position:absolute}
h1,h2,h3,h4{font-family:"Nunito",sans-serif;color:var(--ink)}
.btn{position:absolute;display:inline-flex;align-items:center;justify-content:center;height:32px;padding:0 26px;border-radius:16px;background:var(--navy);color:var(--white);font:700 10px "Roboto",sans-serif;letter-spacing:.3px;text-transform:uppercase;text-decoration:none}
.btn.outline{background:var(--white);color:var(--navy);border:2px solid var(--blue)}
.photo{position:absolute}

/* header */
.site-header{position:absolute;left:0;top:0;width:1200px;height:93px;background:var(--white);z-index:5}
.brand{position:absolute;left:139px;top:30px;display:flex;align-items:center;gap:8px;font:800 22px "Nunito",sans-serif;color:var(--navy)}
.brand .dot{width:16px;height:16px;border-radius:50%;background:var(--sky)}
.contact-row{position:absolute;top:14px;right:124px;display:flex;align-items:center;gap:40px;font:500 12px "Roboto",sans-serif;color:var(--ink)}
.contact-row span{display:flex;align-items:center;gap:8px}
.contact-row .ico{width:18px;height:18px;border-radius:50%;background:var(--blue);display:flex;align-items:center;justify-content:center}
.contact-row .btn{position:static;height:30px;padding:0 28px;background:var(--sky)}
.main-nav{position:absolute;top:63px;left:385px;display:flex;gap:38px;font:700 10.5px "Roboto",sans-serif;text-transform:uppercase;color:var(--ink)}
.main-nav .active{color:var(--blue);border-top:2px solid var(--blue);padding-top:6px;margin-top:-8px}

/* hero */
.hero{position:absolute;left:0;top:93px;width:1200px;height:682px;overflow:hidden}
.hero-photo{left:0;top:0;width:1200px;height:682px;background:linear-gradient(100deg,#f4f8fc 0%,#e7f0f9 40%,#9cc3ee 62%,#3e7fd6 78%,#2c66be 100%)}
.hero h1{position:absolute;left:127px;top:100px;font-size:47px;line-height:55px;font-weight:900;text-transform:uppercase}
.hero .lead{position:absolute;left:127px;top:330px;font:400 20px "Roboto",sans-serif;color:var(--ink)}
.hero .btn{left:127px;top:374px}
.hero .arrows{position:absolute;left:127px;top:440px}

/* service */
.service{position:absolute;left:0;top:775px;width:1200px;height:675px;background:var(--light)}
.service h2{position:absolute;top:96px;width:100%;text-align:center;font-size:27px;font-weight:900;text-transform:uppercase}
.service .intro{position:absolute;top:140px;left:310px;width:580px;text-align:center;font-size:13px;line-height:22px;color:var(--ink)}
.card{position:absolute;top:280px;width:290px;height:258px;background:var(--white);box-shadow:0 8px 24px rgba(20,60,120,.08);text-align:center}
.card .badge{position:absolute;left:105px;top:-22px;width:80px;height:80px;border-radius:50%;background:var(--navy);display:flex;align-items:center;justify-content:center}
.card h3{margin-top:82px;font:700 13px "Roboto",sans-serif;text-transform:uppercase;color:var(--ink)}
.card .sub{margin-top:4px;font-size:13px;color:var(--text)}
.card p{margin:10px auto 0;width:245px;font-size:10px;line-height:18px;color:var(--muted)}
.card .btn{left:50%;transform:translateX(-50%);bottom:-14px;height:28px}
.ring{position:absolute;border:2px solid #a9cbe9;border-radius:50%}

/* repairs */
.repairs{position:absolute;left:0;top:1450px;width:1200px;height:655px;background:var(--white)}
.repairs .block{position:absolute;left:0;top:58px;width:429px;height:534px;background:linear-gradient(135deg,#0d47a1,#1976d2)}
.repairs .frame{position:absolute;left:118px;top:100px;width:510px;height:440px;border:2px solid #8fc0ea}
.repairs .photo{left:85px;top:115px;width:559px;height:421px;background:linear-gradient(120deg,#c8dff0,#8ab4d8 40%,#5a6e86 65%,#d9874a 85%,#f0e8e0)}
.repairs h2{position:absolute;left:715px;top:160px;width:380px;font-size:23px;line-height:32px;font-weight:900;text-transform:uppercase}
.repairs p{position:absolute;left:715px;top:296px;width:360px;font-size:13px;line-height:21px;color:var(--ink)}
.repairs .btn{top:420px;width:110px;padding:0;height:36px;border-radius:18px}

/* faulty */
.faulty{position:absolute;left:0;top:2105px;width:1200px;height:536px;background:linear-gradient(90deg,#eef1f5,#dfe5ec)}
.faulty .photo{left:655px;top:-50px;width:545px;height:586px;background:linear-gradient(160deg,#f2f5f8 0%,#cfdbe8 35%,#2f64b5 60%,#e9eef3 80%,#dfe5ec)}
.faulty h2{position:absolute;left:131px;top:150px;font-size:46px;line-height:56px;font-weight:900;text-transform:uppercase}
.faulty .lead{position:absolute;left:131px;top:268px;font-size:20px;color:var(--ink)}
.faulty .btn{left:131px;top:325px;height:34px}

/* decision */
.decision{position:absolute;left:0;top:2641px;width:1200px;height:745px;background:var(--mist)}
.decision .t1{position:absolute;top:76px;width:100%;text-align:center;font:300 33px "Nunito",sans-serif;color:var(--ink);text-transform:uppercase}
.decision .t2{position:absolute;top:122px;width:100%;text-align:center;font:900 33px "Nunito",sans-serif;color:var(--ink);text-transform:uppercase}
.core{position:absolute;left:471px;top:288px;width:258px;height:258px;border-radius:50%;background:var(--white);box-shadow:0 10px 30px rgba(0,0,0,.08);display:flex;align-items:center;justify-content:center;gap:8px;font:800 24px "Nunito",sans-serif;color:var(--navy)}
.core .dot{width:14px;height:14px;border-radius:50%;background:var(--sky)}
.feat-ico{position:absolute;width:80px;height:80px;border-radius:50%;background:var(--navy);display:flex;align-items:center;justify-content:center;box-shadow:0 0 0 6px rgba(21,101,192,.12)}
.feat{position:absolute;width:270px}
.feat h4{font:700 13px "Roboto",sans-serif;color:var(--ink);text-transform:uppercase}
.feat p{margin-top:6px;font-size:10px;line-height:18px;color:var(--muted)}
.feat.left{text-align:right}

/* outcome */
.outcome{position:absolute;left:0;top:3386px;width:1200px;height:646px;background:var(--white)}
.outcome .block{position:absolute;left:797px;top:84px;width:403px;height:532px;background:linear-gradient(135deg,#1565c0,#0d47a1)}
.outcome .photo{left:582px;top:141px;width:560px;height:422px;background:linear-gradient(135deg,#f4f7fa,#cfe0f3 35%,#3f86e0 55%,#202633 75%,#e4ebf2)}
.outcome h2{position:absolute;left:129px;top:180px;width:300px;font-size:23px;line-height:32px;font-weight:900;text-transform:uppercase}
.checks{position:absolute;left:129px;top:256px;list-style:none}
.checks li{position:relative;padding-left:22px;height:48px}
.checks li::before{content:"";position:absolute;left:0;top:2px;width:10px;height:10px;border-radius:50%;background:var(--blue)}
.checks li::after{content:"";position:absolute;left:3px;top:5px;width:3px;height:2px;border-left:1.5px solid #fff;border-bottom:1.5px solid #fff;transform:rotate(-45deg)}
.checks b{display:block;font:700 10.5px "Roboto",sans-serif;color:var(--navy);text-transform:uppercase}
.checks span{display:block;margin-top:3px;font-size:10.5px;color:var(--text)}

/* help */
.help{position:absolute;left:0;top:4032px;width:1200px;height:700px;background:linear-gradient(90deg,#e9ecef,#e3e7eb)}
.help .photo{left:0;top:0;width:700px;height:640px;background:linear-gradient(110deg,#f4f6f8 0%,#9fb6cd 30%,#5a4637 50%,#e6e9ee 70%,#e3e7eb)}
.help h2{position:absolute;left:715px;top:196px;font-size:46px;line-height:54px;font-weight:900;text-transform:uppercase}
.help .lead{position:absolute;left:715px;top:318px;width:380px;font-size:20px;line-height:26px;color:var(--ink)}
.help .btn{left:715px;top:382px;height:32px}

/* footer */
.site-footer{position:absolute;left:0;top:4560px;width:1200px;height:555px}
.foot-brand{position:absolute;left:130px;top:225px;display:flex;align-items:center;gap:8px;font:800 22px "Nunito",sans-serif;color:var(--white)}
.foot-brand .dot{width:14px;height:14px;border-radius:50%;background:var(--sky)}
.foot-col{position:absolute;top:185px}
.foot-col h4{font:700 12px "Roboto",sans-serif;color:var(--white);text-transform:uppercase;margin-bottom:18px}
.foot-col li{list-style:none;font-size:10.5px;line-height:21px;color:#c8ccd3}
.foot-rule{position:absolute;left:130px;top:397px;width:940px;height:1px;background:#26282d}
.copy{position:absolute;top:440px;width:100%;text-align:center;font-size:13px;color:#dfe2e6}
.socials{position:absolute;top:486px;left:514px;display:flex;gap:10px}
.socials span{width:24px;height:24px;border-radius:50%;border:1.5px solid #dfe2e6}
</style>
</head>
<body>

<header class="site-header">
  <div class="brand"><span class="dot"></span>Lumavex</div>
  <div class="contact-row">
    <span><i class="ico"><svg width="10" height="10" viewBox="0 0 24 24"><path fill="#fff" d="M6.6 10.8a15 15 0 0 0 6.6 6.6l2.2-2.2c.3-.3.7-.4 1-.2 1.1.4 2.3.6 3.6.6.6 0 1 .4 1 1V20c0 .6-.4 1-1 1A17 17 0 0 1 3 4c0-.6.4-1 1-1h3.5c.6 0 1 .4 1 1 0 1.3.2 2.5.6 3.6.1.3 0 .7-.2 1z"/></svg></i>Call Us: +1 555-0142-3380</span>
    <span><i class="ico"><svg width="10" height="10" viewBox="0 0 24 24"><path fill="#fff" d="M2 5h20v14H2z"/><path fill="none" stroke="#1565c0" stroke-width="2" d="M2 5l10 8 10-8"/></svg></i>info@lumavex.de</span>
    <a class="btn" href="#">Purchase</a>
  </div>
  <nav class="main-nav">
    <a class="active">Home</a><a>Endoscope Repair</a><a>Used Endoscopes</a><a>Endoscopy Systems</a><a>Endoscopy Accessories</a>
  </nav>
</header>

<section class="hero">
  <div class="photo hero-photo" role="img" aria-label="Gloved hands holding a flexible endoscope"></div>
  <h1>Put your<br>endoscope<br>in reliable<br>hands!</h1>
  <p class="lead">Cause the outcome matters</p>
  <a class="btn" href="#">Purchase Request</a>
  <svg class="arrows" width="80" height="24" viewBox="0 0 80 24"><g fill="none" stroke="#fff" stroke-width="2"><path d="M28 12H2M9 5l-7 7 7 7"/><path d="M48 12h26M67 5l7 7-7 7"/></g></svg>
  <svg class="abs" style="left:0;top:520px" width="1200" height="162" viewBox="0 0 1200 162">
    <path d="M0 190 L0 120 C180 50 380 60 600 125 C800 180 980 150 1200 60 L1200 190Z" fill="#1565c0"/>
    <path d="M0 190 L0 150 C200 85 400 95 610 155 C810 205 990 170 1200 100 L1200 190Z" fill="#eaf4fb"/>
  </svg>
</section>

<section class="service">
  <h2>Your Future - Our Service</h2>
  <p class="intro">Lumavex GmbH is specialised in the repair and sale of Oriven, Pelmora and Futaro flexible medical endoscopes. As a service-oriented company, we are at your side with our knowledge and skills!</p>

  <article class="card" style="left:129px">
    <div class="badge"><svg width="36" height="36" viewBox="0 0 24 24" fill="none" stroke="#fff" stroke-width="1.5"><path d="M14.7 6.3a4 4 0 0 0 5 5l-8.4 8.4a2 2 0 0 1-2.8-2.8z"/><circle cx="8" cy="8" r="3"/></svg></div>
    <h3>Repair</h3><div class="sub">Endoscope repair service</div>
    <p>Manufacturer-independent we repair and maintain endoscopes, individual components (e.g. processors or light sources), accessories and peripherals of the manufacturers Oriven, Pelmora and Futaro.</p>
    <a class="btn">Learn More</a>
  </article>
  <article class="card" style="left:455px">
    <div class="badge"><svg width="36" height="36" viewBox="0 0 24 24" fill="none" stroke="#fff" stroke-width="1.5"><path d="M3 12V4h8l10 10-8 8z"/><circle cx="7.5" cy="7.5" r="1.5"/></svg></div>
    <h3>Sale</h3><div class="sub">Used endoscopes</div>
    <p>Our regular stock includes refurbished gastroscopes, coloscopes, bronchoscopes, cystoscopes and duodenoscopes from the well-known manufacturers Oriven, Pelmora and Futaro.</p>
    <a class="btn">Purchase Request</a>
  </article>
  <article class="card" style="left:781px">
    <div class="badge"><svg width="36" height="36" viewBox="0 0 24 24" fill="none" stroke="#fff" stroke-width="1.5"><circle cx="12" cy="8" r="4"/><path d="M4 21c0-4 4-7 8-7s8 3 8 7"/></svg></div>
    <h3>Purchase</h3><div class="sub">Used endoscopes</div>
    <p>We are very interested in buying your old endoscopes – even defective and dismantled! We offer fair conditions! Please contact us for a purchase offer!</p>
    <a class="btn">Sell Device</a>
  </article>
  <div class="ring" style="left:1020px;top:490px;width:84px;height:84px"></div>
</section>

<section class="repairs">
  <div class="block"></div>
  <div class="frame"></div>
  <div class="photo" role="img" aria-label="Technician holding an endoscope in front of a processor unit"></div>
  <div class="ring" style="left:594px;top:508px;width:84px;height:84px;background:#fff"></div>
  <h2>Endoscope repairs and second hand endoscopes from Lumavex – cause the outcome matters!</h2>
  <p>Lumavex is a privileged partner for the start-up facility or optimisation of existing healthcare facilities, doctor's offices and hospitals. The quality and reliability of our products and our offered service are our best advertisement!</p>
  <a class="btn outline" style="left:715px">Oriven</a>
  <a class="btn" style="left:840px">Pelmora</a>
  <a class="btn outline" style="left:960px">Futaro</a>
</section>

<section class="faulty">
  <div class="photo" role="img" aria-label="Two doctors looking at a tablet together"></div>
  <h2>Faulty<br>endoscope?</h2>
  <p class="lead">We ensure quick and smooth repairs!</p>
  <a class="btn">Pick-up Order</a>
</section>

<section class="decision">
  <div class="t1">Lumavex GmbH,</div>
  <div class="t2">Your decision for your future</div>
  <svg class="abs" style="left:300px;top:230px" width="600" height="380" viewBox="0 0 600 380"><ellipse cx="300" cy="188" rx="260" ry="180" fill="none" stroke="#b7bcc4" stroke-dasharray="6 6"/></svg>
  <div class="core"><span class="dot"></span>Lumavex</div>

  <div class="feat-ico" style="left:417px;top:234px"><svg width="34" height="34" viewBox="0 0 24 24" fill="none" stroke="#fff" stroke-width="1.5"><circle cx="12" cy="13" r="8"/><path d="M12 9v4l3 2M9 2h6"/></svg></div>
  <div class="feat left" style="left:122px;top:242px"><h4>Fast Repairs</h4><p>Keep potential disruptions in your doctor's office or in your hospital at minimum as a result of optimized processes and highly qualified specialists in our company</p></div>

  <div class="feat-ico" style="left:351px;top:393px"><svg width="34" height="34" viewBox="0 0 24 24" fill="none" stroke="#fff" stroke-width="1.5"><path d="M3 21V9l9-6 9 6v12z"/><path d="M9 21v-6h6v6"/></svg></div>
  <div class="feat left" style="left:62px;top:396px"><h4>On-Site Service</h4><p>We will gladly pay you a visit to to carry out analysis and repairs on site. Due to our many years of experience – it doesn't get any faster (whiglethin a 250 km</p></div>

  <div class="feat-ico" style="left:417px;top:536px"><svg width="34" height="34" viewBox="0 0 24 24" fill="none" stroke="#fff" stroke-width="1.5"><rect x="5" y="4" width="14" height="17" rx="1"/><path d="M9 9h6M9 13h6M9 17h4"/></svg></div>
  <div class="feat left" style="left:122px;top:540px"><h4>Without a<br>maintenance contract</h4><p>No subscription or other maintenance contract, but one-time and sustainable repair work</p></div>

  <div class="feat-ico" style="left:717px;top:234px"><svg width="34" height="34" viewBox="0 0 24 24" fill="none" stroke="#fff" stroke-width="1.5"><circle cx="12" cy="12" r="8"/><path d="M14 9h-3a1.5 1.5 0 0 0 0 3h2a1.5 1.5 0 0 1 0 3h-3M12 7v10"/></svg></div>
  <div class="feat" style="left:814px;top:242px"><h4>Highly Cost Efficient</h4><p>Benefit from our first class recommendations and implementation by our experienced staff. Our goals is to find the best solutions together with you at the best lowest price point.</p></div>

  <div class="feat-ico" style="left:770px;top:393px"><svg width="34" height="34" viewBox="0 0 24 24" fill="none" stroke="#fff" stroke-width="1.5"><path d="M7 21H4V11h3zM7 11l4-8c1.5 0 2.5 1 2.5 2.5V9H19a2 2 0 0 1 2 2.3l-1.3 7.7A2 2 0 0 1 17.7 21H7"/></svg></div>
  <div class="feat" style="left:866px;top:396px"><h4>Loan Equipment Service</h4><p>Use our service of high-quality loan devices during the downtime of your defective endoscope (limited to stock)</p></div>

  <div class="feat-ico" style="left:707px;top:536px"><svg width="34" height="34" viewBox="0 0 24 24" fill="none" stroke="#fff" stroke-width="1.5"><circle cx="12" cy="10" r="6"/><path d="M8 15l-2 7 6-3 6 3-2-7"/></svg></div>
  <div class="feat" style="left:802px;top:540px"><h4>First Class Service</h4><p>Our clients always come first! Sed ut perspiciatis unde omnis iste natus error sit voluptatem accusantium doloremque laudantium</p></div>
</section>

<section class="outcome">
  <div class="block"></div>
  <div class="photo" role="img" aria-label="Gloved hand holding the control section of an endoscope"></div>
  <div class="ring" style="left:548px;top:522px;width:84px;height:84px;background:#fff"></div>
  <h2>Cause the outcome matters!</h2>
  <ul class="checks">
    <li><b>One company for everyone</b><span>We are a service provider for doctors and hospitals!</span></li>
    <li><b>Experience characterises us</b><span>Our team has many years of experience in the business field!</span></li>
    <li><b>The product is close to our hearts</b><span>We repair and sell second hand, flexible endoscopes!</span></li>
    <li><b>Guaranteed service</b><span>You receive a six-month warranty on all repairs!</span></li>
    <li><b>Quality not quantity</b><span>Reliability and durability instead of inferior replacements!</span></li>
    <li><b>Services for everyone</b><span>Our service includes the manufacturers Oriven, Pelmora and Futaro!</span></li>
  </ul>
</section>

<section class="help">
  <div class="photo" role="img" aria-label="Two smiling doctors in conversation"></div>
  <h2>How can<br>we help you?</h2>
  <p class="lead">Sed ut perspiciatis unde omnis iste sit voluptatem accusantium</p>
  <a class="btn">Send us a message!</a>
</section>

<footer class="site-footer">
  <svg class="abs" style="left:0;top:0" width="1200" height="555" viewBox="0 0 1200 555">
    <path d="M0 110 C300 100 700 70 1200 -20 L1200 555 L0 555Z" fill="#1565c0"/>
    <path d="M0 135 C320 125 720 95 1200 10 L1200 555 L0 555Z" fill="#0b0b0d"/>
  </svg>
  <div class="foot-brand"><span class="dot"></span>Lumavex</div>
  <div class="foot-col" style="left:358px"><h4>Quick Links</h4><ul><li>Home</li><li>Endoscope Repair</li><li>Used Endoscopes</li><li>Endoscopy Systems</li><li>Endoscopy Accessories</li><li>Purchase</li></ul></div>
  <div class="foot-col" style="left:534px"><h4>Used Endoscopes</h4><ul><li>Oriven Endoscopes And Processors</li><li>Pelmora Endoscopes And Processors</li><li>Futaro Endoscopes And Processors</li></ul></div>
  <div class="foot-col" style="left:767px"><h4>Contact Us</h4><ul><li>Lumavex GmbH</li><li>Lindenweg 12</li><li>21400 Hafenstedt</li><li>Germany</li></ul></div>
  <div class="foot-col" style="left:938px"><h4>Contact Media</h4><ul><li>Phone +49 4000 555 120-0</li><li>Fax +49 4000 555 120-1</li><li>Email info@lumavex.de</li></ul></div>
  <div class="foot-rule"></div>
  <p class="copy">Lumavex GmbH © 2022. All Rights Reserved.</p>
  <div class="socials"><span></span><span></span><span></span><span></span><span></span></div>
</footer>

</body>
</html>
```